Pellmora Business Cards

Create new business cards with the details below.

Stuart Kovan
Director

MB: +61 427 315 964
PH: 1300 647 519
Email: stuart.kovan@pellmora.com.au
Address: 27D Halden Parade, Brookvale VIC 3174 Australia
Website: www.pellmora.com.au

Target Market(s)

Other business

Industry/Entity Type

Business

Requirements
Must have
• must be clean looking

```html
<!DOCTYPE html>
<html lang="en">
<head>
<meta charset="utf-8">
<title>Pellmora Business Cards</title>
<link rel="stylesheet" href="https://fonts.googleapis.com/css2?family=Roboto:wght@300;400;500;700&display=swap">
<style>
  :root {
    --page: #e4e5e7;
    --charcoal: #333333;
    --lime: #a4cb36;
    --ink: #2b2b2b;
    --ink-soft: #4a4a4a;
    --wood-light: #d9d7d5;
    --wood-mid: #bdbab8;
    --wood-dark: #8f8c8a;
    --white: #ffffff;
  }
  * { margin: 0; padding: 0; box-sizing: border-box; }
  html, body {
    width: 1200px; height: 1200px; overflow: hidden;
    background: var(--page);
    font-family: "Roboto", Arial, sans-serif;
  }
  .sheet { position: relative; width: 1200px; height: 1200px; }
  .card {
    position: absolute; left: 246px;
    width: 708px; height: 394px;
    overflow: hidden; display: flex;
  }
  .card--back { top: 180px; }
  .card--front { top: 626px; }

  .band { height: 100%; flex: none; }
  .band--lime { background: var(--lime); }
  .band--charcoal { background: var(--charcoal); }
  .wood { height: 100%; flex: 1; position: relative; }
  .wood--light { background: linear-gradient(180deg, var(--wood-light), #cfccca 50%, var(--wood-light)); }
  .wood--dark { background: linear-gradient(180deg, var(--wood-mid), var(--wood-dark) 40%, var(--wood-mid) 70%, #a9a6a4); }

  .card--back .band--lime { width: 66px; }
  .card--back .band--charcoal { width: 82px; }

  .brand {
    position: absolute; left: 48px; top: 34px;
  }
  .brand__name {
    display: flex; align-items: center; gap: 14px;
    font-weight: 700; font-size: 56px; letter-spacing: 1px;
    color: var(--lime); line-height: 1;
  }
  .brand__mark { width: 40px; height: 40px; background: var(--charcoal); }
  .brand__tagline {
    margin: 8px 0 0 54px;
    font-weight: 500; font-size: 21px; letter-spacing: 3px;
    color: var(--ink);
  }

  .person { position: absolute; left: 140px; top: 168px; }
  .person__name { font-weight: 300; font-size: 30px; color: var(--ink-soft); letter-spacing: -0.5px; }
  .person__role { font-weight: 500; font-size: 19px; color: var(--ink); margin-top: 2px; }

  .contact { position: absolute; left: 138px; top: 276px; }
  .contact__row { display: flex; gap: 10px; align-items: flex-start; }
  .contact__icon { width: 24px; height: 44px; margin-top: 18px; }
  .contact__lines { font-size: 15.5px; color: var(--ink); line-height: 21px; }
  .contact__label { font-weight: 300; color: var(--ink-soft); }
  .contact__address { margin-top: 4px; font-weight: 300; font-size: 14.5px; color: var(--ink-soft); letter-spacing: -0.2px; }

  .card--front .band--charcoal { width: 397px; position: relative; }
  .card--front .band--lime { width: 101px; box-shadow: -8px 0 12px rgba(0,0,0,0.25); }
  .site {
    position: absolute; left: 66px; top: 180px;
    font-weight: 700; font-size: 27px; color: var(--white);
  }
  .site__tld { font-weight: 500; font-size: 19px; color: var(--lime); }
</style>
</head>
<body>
<main class="sheet">
  <section class="card card--back" aria-label="Card back">
    <div class="band band--lime"></div>
    <div class="band band--charcoal"></div>
    <div class="wood wood--light" role="img" aria-label="Light weathered wood plank texture">
      <div class="brand">
        <div class="brand__name"><span class="brand__mark"></span>PELLMORA</div>
        <div class="brand__tagline">PLANTATION SHUTTERS</div>
      </div>
      <div class="person">
        <div class="person__name">Stuart Kovan</div>
        <div class="person__role">Director</div>
      </div>
      <div class="contact">
        <div class="contact__row">
          <svg class="contact__icon" viewBox="0 0 24 44" aria-hidden="true">
            <rect x="2" y="1" width="20" height="42" rx="3" fill="none" stroke="#2b2b2b" stroke-width="2"/>
            <line x1="2" y1="7" x2="22" y2="7" stroke="#2b2b2b" stroke-width="1.5"/>
            <line x1="2" y1="36" x2="22" y2="36" stroke="#2b2b2b" stroke-width="1.5"/>
            <circle cx="12" cy="39.5" r="1.5" fill="#2b2b2b"/>
          </svg>
          <div class="contact__lines">
            <div>stuart.kovan@pellmora.com.au</div>
            <div><span class="contact__label">MB:</span> +61 427 315 964</div>
            <div><span class="contact__label">PH:</span> 1300 647 519</div>
          </div>
        </div>
        <div class="contact__address">27D Halden Parade, Brookvale VIC 3174, Australia</div>
      </div>
    </div>
  </section>

  <section class="card card--front" aria-label="Card front">
    <div class="band band--charcoal">
      <div class="site">PELLMORA<span class="site__tld">.COM.AU</span></div>
    </div>
    <div class="band band--lime"></div>
    <div class="wood wood--dark" role="img" aria-label="Grey weathered wood plank texture"></div>
  </section>
</main>
</body>
</html>
```